MarbleTrove - New Website Design

Create a professional Vendora website for the hottest trend; a box of school supplies subscription box business called MarbleTrove. Vendora.com is an easy to use website builder.
Please see fizwickpod.com; plumfolly.com; tarrowmintloft.com; and nipcove.com for the concept I am after. The business has not been launched yet, I am currently in the pre-launch stage using a specialized landing page website, and so the time scale for developing my professional looking Vendora website is up to 1-2 weeks.
The webpage should have a fun feel and should match the style of the company logo at plumfolly.com. The pages to include are 'Home', 'About us' and 'Get Started'
Thank you and good luck!
1 page

```html
<!DOCTYPE html>
<html lang="en">
<head>
<meta charset="utf-8">
<title>MarbleTrove – A Box of School Supplies</title>
<link href="https://fonts.googleapis.com/css2?family=Nunito:wght@400;600;700&family=Open+Sans:wght@400;600&display=swap" rel="stylesheet">
<style>
:root{
  --sun:#fbb40b;
  --sun-title:#f6ae0c;
  --gold:#c9a01c;
  --ink:#222222;
  --body:#555555;
  --muted:#8a8a8a;
  --rule:#e3e3e3;
  --white:#ffffff;
  --board-a:#3f8a72;
  --board-b:#1d4a3e;
}
*{margin:0;padding:0;box-sizing:border-box}
html,body{width:1200px;height:3965px;overflow:hidden;background:var(--white)}
body{position:relative;font-family:"Open Sans",Arial,sans-serif;color:var(--body)}
.abs{position:absolute}

/* hero */
.hero{left:0;top:0;width:1200px;height:574px;background:radial-gradient(ellipse at 45% 35%,var(--board-a),var(--board-b) 80%)}
.hero-supplies{left:870px;top:100px;width:230px;height:370px;border-radius:20px;background:linear-gradient(160deg,#e9c94a,#d98b2e 60%,#b84a3a)}
.hero-desk{left:0;top:470px;width:1200px;height:104px;background:linear-gradient(90deg,#6b8fb8,#c7a06c 40%,#8a6e9e 70%,#5b7fa8)}
.brand{left:190px;top:18px;display:flex;align-items:center;gap:12px;color:var(--white);font:700 24px "Nunito",Arial,sans-serif}
.brand-mark{width:48px;height:48px;border-radius:10px;background:var(--sun)}
.nav{left:610px;top:34px;display:flex;gap:34px;font:600 14px "Nunito",Arial,sans-serif;color:var(--white)}
.nav-icons{left:945px;top:32px;display:flex;gap:22px}
.hero-title{left:0;width:1200px;top:222px;text-align:center;color:var(--white);font:400 26px "Nunito",Arial,sans-serif;letter-spacing:1px}
.hero-sub{left:0;width:1200px;top:268px;text-align:center;color:#e7efe9;font-size:14px}
.btn{display:flex;align-items:center;justify-content:center;background:var(--gold);color:var(--white);font:600 12px "Nunito",Arial,sans-serif;text-transform:uppercase}
.hero-btn{left:520px;top:309px;width:160px;height:51px;background:#f5b00d}
.scroll-down{left:585px;top:455px}

/* intro */
.intro{left:278px;top:632px;width:648px;text-align:center;font-size:13.5px;line-height:24px;color:var(--ink)}

.section-title{left:0;width:1200px;text-align:center;color:var(--sun-title);font:400 36px "Nunito",Arial,sans-serif}
.title-rule{left:555px;width:90px;height:1px;background:var(--rule)}

/* products */
.card{border:1px solid #eeeeee;border-radius:6px;background:var(--white);overflow:hidden;padding:14px}
.photo{width:100%;height:100%;border-radius:4px}
.label{text-align:center;font:700 13px "Nunito",Arial,sans-serif;color:var(--ink)}

/* newsletter */
.newsletter{left:0;top:2128px;width:1200px;height:409px;background:var(--sun)}
.news-title{left:0;width:1200px;top:2222px;text-align:center;color:var(--white);font:400 36px "Nunito",Arial,sans-serif}
.news-sub{left:0;width:1200px;top:2280px;text-align:center;color:#fde3a0;font-size:13px}
.news-rule{left:555px;top:2318px;width:90px;height:1px;background:#fdd77a}
.news-form{left:338px;top:2358px;width:526px;height:66px;background:var(--white);border:1px solid var(--white);display:flex;align-items:center;padding:0 8px 0 24px}
.news-input{flex:1;font-size:13px;color:var(--muted)}
.news-btn{width:148px;height:52px;font-size:14px;text-transform:none}

/* blog */
.post-title{font:600 14px "Nunito",Arial,sans-serif;color:var(--ink);line-height:24px;text-transform:uppercase}
.post-text{font-size:13.5px;line-height:24px;color:var(--body)}
.post-btn{width:145px;height:53px;font-size:14px}

/* footer */
.footer-list{list-style:none;font-size:11.5px;color:var(--ink);line-height:35px}
.social li{display:flex;align-items:center;gap:14px}
.social-dot{width:10px;height:10px;border-radius:50%;background:var(--ink)}
.cards{left:830px;top:3750px;display:flex;gap:8px}
.pay-card{width:29px;height:18px;border-radius:3px;background:#7a7a7a}
.foot-copy{font-size:11px;color:var(--ink)}
.foot-rule{left:204px;top:3914px;width:795px;height:1px;background:var(--rule)}
</style>
</head>
<body>

<header>
  <div class="abs hero"></div>
  <div class="abs hero-supplies" role="img" aria-label="Yellow cup full of coloured pencils, scissors and a ruler"></div>
  <div class="abs hero-desk" role="img" aria-label="Desk covered with markers, crayons and notebooks"></div>
  <div class="abs brand"><span class="brand-mark"></span>MarbleTrove</div>
  <nav class="abs nav"><span>Shop</span><span>About Us</span><span>Blog</span><span>Contact Us</span></nav>
  <div class="abs nav-icons">
    <svg width="16" height="16" viewBox="0 0 16 16"><circle cx="6.5" cy="6.5" r="5" fill="none" stroke="#fff" stroke-width="2"/><line x1="10.5" y1="10.5" x2="15" y2="15" stroke="#fff" stroke-width="2"/></svg>
    <svg width="16" height="16" viewBox="0 0 16 16"><path d="M3 5h10l-1 10H4z M6 5V3a2 2 0 0 1 4 0v2" fill="none" stroke="#fff" stroke-width="1.6"/></svg>
  </div>
  <h1 class="abs hero-title">A BOX OF SCHOOL SUPPLIES</h1>
  <p class="abs hero-sub">Sed ut perspiciatis unde omnis iste natus error sit voluptatem</p>
  <div class="abs btn hero-btn">Shop Now</div>
  <svg class="abs scroll-down" width="30" height="30" viewBox="0 0 30 30"><circle cx="15" cy="15" r="13" fill="none" stroke="#fff" stroke-width="2"/><polyline points="9,13 15,19 21,13" fill="none" stroke="#fff" stroke-width="2"/></svg>
</header>

<p class="abs intro">Wellcome to MarbleTrove omnis iste natus error sit voluptatem accusantium doloremque laudantium, totam rem aperiam, eaque ipsa quae ab illo inventore veritatis et quasi architecto beatae vitae dicta sunt explicabo. Nemo enim ipsam voluptatem quia voluptas sit aspernatur aut odit aut fugit</p>

<section>
  <h2 class="abs section-title" style="top:768px">Featured Products</h2>
  <div class="abs title-rule" style="top:835px"></div>

  <div class="abs card" style="left:204px;top:883px;width:219px;height:201px"><div class="photo" role="img" aria-label="Pencil case with pencils, sticky notes and erasers" style="background:linear-gradient(135deg,#f3d36b,#e8708a 50%,#5b6b8a)"></div></div>
  <div class="abs label" style="left:204px;top:1096px;width:219px">MarbleTrove 1 - $ 62.00</div>

  <div class="abs card" style="left:204px;top:1144px;width:219px;height:204px"><div class="photo" role="img" aria-label="Pencil cup on a stack of notebooks" style="background:linear-gradient(135deg,#f1a43a,#6bb56b 50%,#5c8ad0)"></div></div>
  <div class="abs label" style="left:204px;top:1360px;width:219px">MarbleTrove 2 - $ 22.00</div>

  <div class="abs card" style="left:447px;top:883px;width:552px;height:457px;padding:90px 140px"><div class="photo" role="img" aria-label="Wooden crate filled with school supplies" style="background:linear-gradient(160deg,#3a78c8,#e85a5a 40%,#d7b07a 60%,#b58a55)"></div></div>
  <div class="abs label" style="left:447px;top:1360px;width:552px">MarbleTrove 3 - $ 22.00</div>

  <div class="abs card" style="left:204px;top:1485px;width:549px;height:458px;padding:80px 120px"><div class="photo" role="img" aria-label="Pencil holder with coloured pencils on notebooks and scissors" style="background:linear-gradient(160deg,#444,#e0463e 45%,#f0c04a 65%,#4ab06a)"></div></div>
  <div class="abs label" style="left:204px;top:1965px;width:549px">MarbleTrove 4 - $ 22.00</div>

  <div class="abs card" style="left:777px;top:1485px;width:222px;height:199px"><div class="photo" role="img" aria-label="Desk organiser with pens, scissors and notepads" style="background:linear-gradient(135deg,#333,#e04848 50%,#f2c64c)"></div></div>
  <div class="abs label" style="left:777px;top:1698px;width:222px">MarbleTrove 5 - $ 62.00</div>

  <div class="abs card" style="left:777px;top:1747px;width:222px;height:201px"><div class="photo" role="img" aria-label="Globe, books and crayons" style="background:linear-gradient(135deg,#3f7ed0,#f2c14a 50%,#e0503e)"></div></div>
  <div class="abs label" style="left:777px;top:1965px;width:222px">MarbleTrove 6 - $ 22.00</div>
</section>

<section>
  <div class="abs newsletter"></div>
  <h2 class="abs news-title">Subscribe to our newsletter</h2>
  <p class="abs news-sub">Sed ut perspiciatis unde omnis iste natus error sit voluptatem</p>
  <div class="abs news-rule"></div>
  <div class="abs news-form"><span class="news-input">Enter Your E-mail Address</span><span class="btn news-btn">Subscribe Now</span></div>
</section>

<section>
  <h2 class="abs section-title" style="top:2644px">From the blog</h2>
  <div class="abs title-rule" style="top:2706px"></div>

  <h3 class="abs post-title" style="left:201px;top:2822px;width:320px">Sed ut perspiciatis unde omnis iste natus error sit</h3>
  <p class="abs post-text" style="left:201px;top:2890px;width:315px">Doloremque laudantium, totam rem aperiam, eaque ipsa quae ab illo inventore veritatis et quasi architecto beatae vitae dicta sunt explicabo. Nemo enim ipsam voluptatem quia voluptas sit aspernatur aut odit aut fugit, sed quia</p>
  <div class="abs btn post-btn" style="left:201px;top:3042px">Read More</div>
  <div class="abs" role="img" aria-label="Two schoolgirls smiling in a classroom" style="left:611px;top:2778px;width:388px;height:370px;background:linear-gradient(135deg,#6aa8e0,#e9c79a 50%,#f0d44a)"></div>

  <div class="abs" role="img" aria-label="Children with backpacks running down a school corridor" style="left:201px;top:3235px;width:388px;height:368px;background:linear-gradient(135deg,#c99a62,#e8d8b8 45%,#7a8fb0)"></div>
  <h3 class="abs post-title" style="left:608px;top:3266px;width:330px">Sed ut perspiciatis unde omnis iste natus error sit</h3>
  <p class="abs post-text" style="left:608px;top:3332px;width:318px">Doloremque laudantium, totam rem aperiam, eaque ipsa quae ab illo inventore veritatis et quasi architecto beatae vitae dicta sunt explicabo. Nemo enim ipsam voluptatem quia voluptas sit aspernatur aut odit aut fugit, sed quia</p>
  <div class="abs btn post-btn" style="left:608px;top:3484px">Read More</div>
</section>

<footer>
  <div class="abs title-rule" style="top:3684px"></div>
  <ul class="abs footer-list" style="left:204px;top:3735px"><li>Shop</li><li>About Us</li><li>Blog</li><li>Contact Us</li></ul>
  <ul class="abs footer-list" style="left:383px;top:3735px"><li>Privacy Policy</li><li>Shipping &amp; Return Policy</li><li>Terms of Service</li></ul>
  <ul class="abs footer-list social" style="left:608px;top:3735px">
    <li><span class="social-dot"></span>Friendwall</li>
    <li><span class="social-dot"></span>Chirpline</li>
    <li><span class="social-dot"></span>Pinboardly</li>
    <li><span class="social-dot"></span>Snapgrid</li>
  </ul>
  <div class="abs cards"><span class="pay-card"></span><span class="pay-card"></span><span class="pay-card"></span><span class="pay-card"></span><span class="pay-card"></span></div>
  <p class="abs foot-copy" style="left:794px;top:3778px">© 2017 Company Name | All Rights Reserved</p>
  <div class="abs foot-rule"></div>
  <p class="abs foot-copy" style="left:0;width:1200px;top:3928px;text-align:center">© 2017 Company Name | All Rights Reserved</p>
</footer>

</body>
</html>
```